Business Card Design

We need a business card designed for our new company. Prefer a black card with white logo & writing.

Contact Information for Business Card

Ted Galloway, address: 7-4812 Fernhollow Road, Abbotsford, BC, V3K 8R2, Office Phone: 604-712-3390, Cell: 604-947-2164, Email: ted@resinworkshub.ca

Colors

Designer to choose only greyscale colors for use in the design.

```html
<!DOCTYPE html>
<html lang="en">
<head>
<meta charset="utf-8">
<title>Resinworks Hub – Business Card</title>
<link href="https://fonts.googleapis.com/css2?family=Figtree:wght@400;700;800&display=swap" rel="stylesheet">
<style>
  :root {
    --backdrop: #1f1f1f;
    --card: #000000;
    --ink: #ffffff;
    --ink-soft: #e6e6e6;
    --art-top: #1a1a1a;
    --art-bottom: #8a8a8a;
  }
  html, body {
    margin: 0;
    padding: 0;
    width: 1200px;
    height: 900px;
    overflow: hidden;
    background: var(--backdrop);
    font-family: "Figtree", sans-serif;
    color: var(--ink);
  }
  .stage {
    position: relative;
    width: 1200px;
    height: 900px;
  }
  .card {
    position: absolute;
    top: 192px;
    width: 296px;
    height: 518px;
    background: var(--card);
    overflow: hidden;
  }
  .card--front { left: 292px; }
  .card--back { left: 614px; }

  .centered {
    position: absolute;
    left: 0;
    right: 0;
    text-align: center;
  }
  .holder-name {
    top: 82px;
    margin: 0;
    font-size: 20px;
    font-weight: 800;
    letter-spacing: 0.2px;
  }
  .holder-title {
    top: 106px;
    margin: 0;
    font-size: 13.5px;
    font-weight: 400;
    color: var(--ink-soft);
  }
  .divider {
    position: absolute;
    top: 135px;
    left: 131px;
    width: 34px;
    height: 1.5px;
    background: var(--ink);
  }
  .address {
    top: 152px;
    margin: 0;
    font-size: 14px;
    line-height: 18px;
    font-style: normal;
  }
  .contact-icons {
    top: 211px;
    display: flex;
    justify-content: center;
    gap: 8px;
  }
  .contact-icons svg { width: 18px; height: 18px; display: block; }
  .contact-list {
    top: 236px;
    margin: 0;
    padding: 0;
    list-style: none;
    font-size: 14px;
    line-height: 18px;
  }
  .summit-art {
    position: absolute;
    left: 0;
    right: 0;
    top: 362px;
    height: 128px;
    background: linear-gradient(180deg, var(--art-top) 0%, var(--art-bottom) 100%);
  }

  .brand {
    top: 240px;
    display: flex;
    justify-content: center;
    align-items: center;
    gap: 10px;
  }
  .brand-mark {
    width: 14px;
    height: 14px;
    border-radius: 50%;
    background: var(--ink);
  }
  .brand-name {
    margin: 0;
    font-size: 25px;
    font-weight: 800;
    letter-spacing: 0.5px;
    text-transform: uppercase;
  }
  .back-url {
    top: 471px;
    margin: 0;
    font-size: 13.5px;
  }
</style>
</head>
<body>
<main class="stage">
  <section class="card card--front" aria-label="Card front">
    <h1 class="centered holder-name">TED GALLOWAY</h1>
    <p class="centered holder-title">President</p>
    <span class="divider"></span>
    <address class="centered address">7-4812 Fernhollow Road<br>Abbotsford, BC, V3K 8R2</address>
    <div class="centered contact-icons" aria-hidden="true">
      <svg viewBox="0 0 18 18"><circle cx="9" cy="9" r="9" fill="#fff"/><path d="M6 4.5c.6-.3 1 0 1.3.6l.6 1.3c.2.5 0 .9-.4 1.2l-.4.3c.4 1 1.2 1.8 2.1 2.2l.3-.4c.3-.4.7-.6 1.2-.4l1.3.6c.6.3.8.7.5 1.3-.5 1-1.4 1.4-2.5 1-2.2-.8-3.9-2.5-4.7-4.7-.4-1.1 0-2 .7-2.6z" fill="#000"/></svg>
      <svg viewBox="0 0 18 18"><circle cx="9" cy="9" r="9" fill="#fff"/><rect x="6.2" y="3.8" width="5.6" height="10.4" rx="1" fill="none" stroke="#000" stroke-width="1.1"/><circle cx="9" cy="12.6" r=".6" fill="#000"/></svg>
      <svg viewBox="0 0 18 18"><circle cx="9" cy="9" r="9" fill="#fff"/><rect x="4.5" y="5.8" width="9" height="6.4" rx=".8" fill="#000"/><path d="M4.8 6.2 9 9.3l4.2-3.1" fill="none" stroke="#fff" stroke-width=".9"/></svg>
      <svg viewBox="0 0 18 18"><circle cx="9" cy="9" r="9" fill="#fff"/><g fill="none" stroke="#000" stroke-width=".9"><circle cx="9" cy="9" r="5"/><ellipse cx="9" cy="9" rx="2.2" ry="5"/><path d="M4 9h10M4.8 6.5h8.4M4.8 11.5h8.4"/></g></svg>
    </div>
    <ul class="centered contact-list">
      <li>604-712-3390</li>
      <li>604-947-2164</li>
      <li>ted@resinworkshub.ca</li>
      <li>www.resinworkshub.ca</li>
    </ul>
    <div class="summit-art" role="img" aria-label="Snow-capped mountain peak illustration in white on black"></div>
  </section>

  <section class="card card--back" aria-label="Card back">
    <div class="centered brand">
      <span class="brand-mark"></span>
      <p class="brand-name">Resinworks Hub</p>
    </div>
    <p class="centered back-url">www.resinworkshub.ca</p>
  </section>
</main>
</body>
</html>
```